Business Cards Needed for Innovative Healthcare Marketing Company

We are a marketing company focused on healthcare. Our company is all about rebranding yourself renewing your image and generating results. The phoenix stands for "reborn" or "rising" which we provide new brands for our clients we take their old brands and renew it with creativity and innovation. I am looking for a business card with color dimension. I have attached an example of a card I think has the look and feel of what I am trying to accomplish. I like that the card example has black and grey font colors, I like the font placement and the small logo, I really like the use of the colors on the right those are the colors of my logo. My logo is phoenix so maybe incorporating flames similar to that design. I would like the back a solid color maybe red with an opaque version of the logo and website. As a marketing company I am always open to creative liberty!

Target Market(s)

Doctors and business professionals.

Industry/Entity Type

Marketing

Contact Information for Business Card

Valcorne Health Care Marketing
Marla Tenwick- CEO
#(512)638-2974
email-marla@valcorne.com
website- valcorne.com

Font styles to use
Sans Serif

Colors
ec1f27
f37122
ffc214
fbed22
fbf289
f04a50

Requirements
Must have
• The logo and required information
Nice to have
• icons by the information
Should not have
• child like font

```html
<!DOCTYPE html>
<html lang="en">
<head>
<meta charset="utf-8">
<title>Valcorne Health Care Marketing – Business Card</title>
<link rel="stylesheet" href="https://fonts.googleapis.com/css2?family=Josefin+Sans:wght@300&family=Open+Sans:wght@400;600&display=swap">
<style>
  :root {
    --canvas: #ecebe8;
    --brand-red: #9d1c20;
    --brand-red-deep: #a8201f;
    --brand-red-warm: #c43d1f;
    --brand-orange: #f4931f;
    --brand-orange-deep: #e8792a;
    --paper: #ffffff;
    --ink-light: #ffffff;
    --ink-muted: #f3d9d6;
  }
  * { box-sizing: border-box; margin: 0; padding: 0; }
  html, body { width: 1200px; height: 900px; overflow: hidden; }
  body { background: var(--canvas); position: relative; font-family: "Open Sans", sans-serif; }

  .card { position: absolute; overflow: hidden; box-shadow: 0 6px 18px rgba(0,0,0,.18); }

  /* Front */
  .card-front { left: 238px; top: 62px; width: 555px; height: 342px; background: var(--brand-red); color: var(--ink-light); }
  .front-art { position: absolute; inset: 0; width: 555px; height: 342px; }
  .brand-block { position: absolute; left: 34px; top: 38px; }
  .brand-name { font-family: "Josefin Sans", sans-serif; font-weight: 300; font-size: 44px; letter-spacing: 1px; line-height: 1; color: var(--ink-light); }
  .brand-tagline { font-family: "Josefin Sans", sans-serif; font-weight: 300; font-size: 14.5px; letter-spacing: .6px; margin-top: 12px; color: var(--ink-light); }
  .person { position: absolute; left: 34px; top: 157px; }
  .person-name { font-weight: 600; font-size: 20px; line-height: 1.2; }
  .person-role { font-size: 15px; line-height: 1.3; padding-left: 1px; }
  .contact-list { position: absolute; left: 36px; top: 234px; list-style: none; }
  .contact-item { display: flex; align-items: center; gap: 9px; font-size: 16px; line-height: 23px; }
  .contact-icon { width: 11px; height: 11px; fill: var(--ink-light); flex: none; }

  /* Back */
  .card-back { left: 457px; top: 518px; width: 560px; height: 342px; background: var(--paper); }
  .band-top { position: absolute; left: 0; top: 0; width: 100%; height: 99px; background: linear-gradient(var(--brand-orange), var(--brand-orange-deep)); }
  .band-bottom { position: absolute; left: 0; bottom: 0; width: 100%; height: 97px; background: linear-gradient(var(--brand-red-warm), var(--brand-red-deep)); }
  .back-brand { position: absolute; left: 0; top: 99px; width: 100%; height: 146px; display: flex; align-items: center; justify-content: center; gap: 16px; }
  .back-dot { width: 46px; height: 46px; border-radius: 50%; background: var(--brand-orange); }
  .back-text { color: var(--brand-red); }
  .back-name { font-family: "Josefin Sans", sans-serif; font-weight: 300; font-size: 54px; letter-spacing: 1px; line-height: 1; }
  .back-tagline { font-family: "Josefin Sans", sans-serif; font-weight: 300; font-size: 17px; letter-spacing: .8px; margin-top: 10px; }
</style>
</head>
<body>

<section class="card card-front">
  <svg class="front-art" viewBox="0 0 555 342" role="img" aria-label="Phoenix rising in flames illustration in orange and red">
    <defs>
      <linearGradient id="flameTone" x1="0" y1="0" x2="1" y2="1">
        <stop offset="0" stop-color="#f5951f"/>
        <stop offset="1" stop-color="#ef8a1e"/>
      </linearGradient>
    </defs>
    <path d="M300 0 H555 V342 H255 C250 290 262 240 280 200 C300 150 285 90 300 0 Z" fill="url(#flameTone)"/>
  </svg>

  <div class="brand-block">
    <div class="brand-name">VALCORNE</div>
    <div class="brand-tagline">HEALTH CARE MARKETING</div>
  </div>

  <div class="person">
    <div class="person-name">Marla Tenwick</div>
    <div class="person-role">CEO</div>
  </div>

  <ul class="contact-list">
    <li class="contact-item">
      <svg class="contact-icon" viewBox="0 0 12 12"><path d="M2.4 0.6 L4.2 2.6 L3.2 4 C3.9 5.6 5.2 6.9 6.8 7.6 L8.2 6.6 L10.4 8.4 L9.4 10.6 C5 10.4 1.2 6.6 0.8 1.8 Z"/></svg>
      <span>(512)638-2974</span>
    </li>
    <li class="contact-item">
      <svg class="contact-icon" viewBox="0 0 12 12"><path d="M0.5 2.5 H11.5 V9.5 H0.5 Z M1 3 L6 6.8 L11 3" stroke="#9d1c20" stroke-width=".9"/></svg>
      <span>marla@valcorne.com</span>
    </li>
    <li class="contact-item">
      <svg class="contact-icon" viewBox="0 0 12 12"><circle cx="6" cy="6" r="5.5"/><path d="M0.5 6 H11.5 M6 0.5 C3.5 3.5 3.5 8.5 6 11.5 M6 0.5 C8.5 3.5 8.5 8.5 6 11.5" stroke="#9d1c20" stroke-width=".8" fill="none"/></svg>
      <span>valcorne.com</span>
    </li>
  </ul>
</section>

<section class="card card-back">
  <div class="band-top"></div>
  <div class="back-brand">
    <div class="back-dot"></div>
    <div class="back-text">
      <div class="back-name">VALCORNE</div>
      <div class="back-tagline">HEALTH CARE MARKETING</div>
    </div>
  </div>
  <div class="band-bottom"></div>
</section>

</body>
</html>
```